SOLVE Study flyer

I need help designing a flyer for a research study that will include brain imaging in adolescents. The info is in the attached document. The study is called the Sequoia Outlook Lantern Valley Echo (SOLVE) study. Ideally this would be returned as a document that I can edit in the future as we will have several new recruitment phases (different age groups, etc. I also would love to have a logo designed as part of this project, but I recognize that might be a separate design request.

```html
<!DOCTYPE html>
<html lang="en">
<head>
<meta charset="utf-8">
<title>SOLVE Study Flyer</title>
<link href="https://fonts.googleapis.com/css2?family=Poppins:wght@400;500;600;700;800&display=swap" rel="stylesheet">
<style>
:root{
  --navy:#0f1d45;
  --navy-text:#1b3563;
  --purple:#6b489c;
  --purple-light:#7a57b0;
  --lavender:#e1ddef;
  --lavender-bright:#cabfe8;
  --grey:#6a6a6a;
  --ink:#141414;
  --white:#ffffff;
}
*{margin:0;padding:0;box-sizing:border-box}
html,body{width:927px;height:1200px;overflow:hidden;background:var(--white)}
.flyer{position:relative;width:927px;height:1200px;font-family:"Poppins",sans-serif;color:var(--ink);overflow:hidden}
.backdrop{position:absolute;left:0;top:0}
.wordmark{position:absolute;left:28px;top:30px;font-size:100px;font-weight:800;letter-spacing:-2px;line-height:1;
  background:linear-gradient(180deg,#5b3a93 0%,#1a1f4f 100%);-webkit-background-clip:text;background-clip:text;color:transparent}
.rule{position:absolute;left:0;top:147px;width:380px;height:2px;background:var(--purple)}
.rule::after{content:"";position:absolute;right:-4px;top:-3.5px;width:9px;height:9px;border-radius:50%;background:var(--purple)}
.diamonds{position:absolute;left:403px;top:128px;width:43px;height:43px;background:var(--purple)}
.study-name{position:absolute;left:27px;top:172px;font-size:22px;font-weight:600;color:var(--navy-text);line-height:36px}
.question{position:absolute;left:29px;top:257px;font-size:21px;font-weight:600}
.question span{color:var(--purple-light)}
.pill{position:absolute;left:28px;top:313px;width:412px;height:100px;border-radius:50px;background:var(--purple)}
.pill-badge{position:absolute;left:12px;top:10px;width:80px;height:80px;border-radius:50%;background:var(--navy)}
.pill-text{position:absolute;left:123px;top:20px;font-size:19.5px;color:var(--white);line-height:29px}
.intro{position:absolute;left:27px;top:434px;width:420px;font-size:17.5px;color:var(--grey);line-height:29px}
.tagline{position:absolute;left:716px;top:501px;width:152px;height:152px;border-radius:50%;background:var(--lavender);
  display:flex;align-items:center;justify-content:center;text-align:center;font-size:11.5px;line-height:22px;color:var(--ink)}
.heading{position:absolute;left:28px;font-size:26.5px;font-weight:700;color:var(--navy);letter-spacing:.2px}
.heading.involves{top:574px}
.heading.eligible{top:770px;left:30px}
.bullets{position:absolute;left:28px;top:632px;width:870px;list-style:none;font-size:13.5px;line-height:22px}
.bullets li{position:relative;padding-left:26px;margin-bottom:12px}
.bullets li::before,.criteria li::before{content:"";position:absolute;left:1px;top:6px;width:10px;height:10px;border-radius:50%;background:var(--purple)}
.criteria{position:absolute;left:28px;top:827px;display:flex;list-style:none;font-size:13px;line-height:22px}
.criteria li{position:relative;padding-left:22px;margin-right:20px}
.contact{position:absolute;left:27px;top:880px;width:873px;height:248px;border:2px solid var(--navy);border-radius:42px;background:var(--lavender)}
.invite{position:absolute;left:36px;top:30px;font-size:34px;font-weight:600;line-height:49px;color:var(--navy)}
.invite em{font-style:normal;color:var(--purple-light)}
.contact-label{position:absolute;left:36px;top:136px;font-size:16px;font-weight:700;color:var(--ink)}
.email{position:absolute;left:36px;top:172px;display:flex;align-items:center;gap:11px;font-size:27px;color:var(--navy)}
.reward{position:absolute;left:525px;top:11px;width:334px;height:222px;border-radius:30px;
  background:linear-gradient(160deg,#1a1f4f 0%,#3a2e72 55%,#63449a 100%);box-shadow:0 3px 6px rgba(0,0,0,.25)}
.reward-label{position:absolute;left:29px;top:22px;padding:2px 15px;border:1px solid rgba(255,255,255,.7);border-radius:8px;font-size:19px;color:var(--white)}
.reward-amount{position:absolute;left:26px;top:44px;font-size:122px;font-weight:700;letter-spacing:-3px;color:var(--lavender-bright);line-height:1.2}
.reward-note{position:absolute;right:30px;top:184px;font-size:13px;color:var(--white)}
.university{position:absolute;left:51px;top:1152px;font-size:19px;font-weight:600;color:var(--navy)}
.department{position:absolute;left:364px;top:1146px;font-size:13px;line-height:22px;color:var(--ink)}
.review{position:absolute;left:581px;top:1144px;font-size:13px;line-height:22px;color:var(--purple-light)}
.code{position:absolute;right:6px;bottom:3px;font-size:6px;color:var(--ink)}
</style>
</head>
<body>
<div class="flyer">
  <svg class="backdrop" width="927" height="1200" viewBox="0 0 927 1200">
    <defs>
      <linearGradient id="nightSky" x1="0" y1="1" x2="1" y2="0">
        <stop offset="0" stop-color="#121a45"/>
        <stop offset="1" stop-color="#5b3c93"/>
      </linearGradient>
      <radialGradient id="brainScan" cx=".55" cy=".4" r=".65">
        <stop offset="0" stop-color="#4fa4ef"/>
        <stop offset=".55" stop-color="#1d4fb0"/>
        <stop offset="1" stop-color="#07123a"/>
      </radialGradient>
    </defs>
    <path d="M466 0 C540 160 700 250 800 330 C880 400 870 600 905 670 L927 670 L927 0 Z" fill="url(#nightSky)"/>
    <path d="M790 640 C840 660 880 668 927 668 L927 670 L790 670 Z" fill="url(#nightSky)"/>
    <circle cx="712" cy="350" r="248" fill="#ffffff"/>
    <circle cx="707" cy="352" r="243" fill="url(#brainScan)" role="img" aria-label="Illustration of a glowing blue human head and brain in profile, showing the developing brain"/>
  </svg>

  <div class="wordmark">SOLVE</div>
  <div class="rule"></div>
  <div class="diamonds" role="img" aria-label="Decorative diamond pattern"></div>

  <h2 class="study-name">Sequoia Outlook Lantern<br>Valley Echo Study</h2>
  <p class="question">Are you the parent of a child age <span>10-17?</span></p>

  <div class="pill">
    <div class="pill-badge" role="img" aria-label="Icon of a head with brain"></div>
    <p class="pill-text">Do they worry or overthink<br>negative emotions?</p>
  </div>

  <p class="intro">Northbridge University researchers are seeking girls age 10-17 for a study about brain activity in emotions and decision-making and how they relate to puberty, anxiety and depression.</p>

  <div class="tagline">Advancing<br>understanding of<br>the developing brain<br>and mental health</div>

  <h3 class="heading involves">STUDY PARTICIPATION INVOLVES:</h3>
  <ul class="bullets">
    <li>ONE ONE-HOUR INTERVIEW (ONLINE OR IN-PERSON) where your child will discuss their thoughts</li>
    <li>Online Questionnaires (Parent And Child)</li>
    <li>One two-hour visit where your child will complete an MRI scan, answer questions about their puberty stage, and have a small hair sample taken to study puberty hormones.</li>
  </ul>

  <h3 class="heading eligible">YOUR CHILD MAY BE ELIGIBLE IF THEY:</h3>
  <ul class="criteria">
    <li>Are age 10-17</li>
    <li>Tend to worry or overthink negative thoughts</li>
    <li>Have not been diagnosed with psychosis, learning problems, or autism</li>
  </ul>

  <section class="contact">
    <p class="invite"><em>Interested</em> In Participating?<br>Want More <em>Information?</em></p>
    <p class="contact-label">PLEASE CONTACT US!</p>
    <p class="email">
      <svg width="26" height="20" viewBox="0 0 26 20" aria-hidden="true">
        <rect x="0" y="0" width="26" height="20" rx="3" fill="#6b489c"/>
        <path d="M1 2 L13 11 L25 2" fill="none" stroke="#e1ddef" stroke-width="2"/>
      </svg>
      solvestudy@northbridge.edu
    </p>
    <div class="reward">
      <span class="reward-label">Compensation Up To</span>
      <span class="reward-amount">$140</span>
      <span class="reward-note">For Participation</span>
    </div>
  </section>

  <p class="university">Northbridge University</p>
  <p class="department">Department of Psychiatry<br>School of Medicine</p>
  <p class="review">This study has been reviewed by the Northbridge<br>University Institutional Review Board</p>
  <span class="code">C70</span>
</div>
</body>
</html>
```